New Bicycle shop business card

Hi!
I'm looking for a business card for my new proffesional bike mechanics shop. This shop is only for fixing broken bikes and not selling bikes.
Peferbly a modern and sleek and modern design.
Colors: black, grey, red, white
Information:
Name: Rijwielwerkplaats Vanhoutte
Shop owner: Bart Vanhoutte & Marieke Segers
Website: www.rijwielwerkplaats-vanhoutte.be
Email: info@rijwielwerkplaats-vanhoutte.be
Phone number: +32471902368
Street adres: Kerkweg 46
9940 Bellebeke
Slogan/shop information: Herstellingen van alle merken.
Logo: see files.
Target Market(s)
People who seek a mechanic to fix or upgrade their bikes.
Contact Information for Business Card
Information:
Website: info@rijwielwerkplaats-vanhoutte.be
9940 Bellebeke
Logo: see files.

```html
<!DOCTYPE html>
<html lang="nl">
<head>
<meta charset="UTF-8">
<title>Rijwielwerkplaats Vanhoutte – Visitekaartje</title>
<link rel="stylesheet" href="https://fonts.googleapis.com/css2?family=Montserrat:wght@600;700&family=Roboto:wght@400&display=swap">
<style>
  :root {
    --backdrop: #2c2c2e;
    --card: #1c1c1e;
    --red: #e0313f;
    --white: #ffffff;
    --grey: #8e9396;
    --emboss: #3a3a3d;
  }
  * { margin: 0; padding: 0; box-sizing: border-box; }
  html, body {
    width: 799px;
    height: 1200px;
    overflow: hidden;
    background: var(--backdrop);
  }
  .canvas {
    width: 799px;
    height: 1200px;
    display: flex;
    flex-direction: column;
    align-items: center;
    justify-content: space-around;
    padding: 60px 0;
  }
  .card {
    position: relative;
    width: 620px;
    height: 354px;
    background: var(--card);
    border-radius: 24px;
    overflow: hidden;
  }
  /* Front */
  .card-front {
    display: flex;
    align-items: center;
    justify-content: center;
  }
  .front-name {
    font-family: 'Montserrat', sans-serif;
    font-weight: 700;
    font-size: 26px;
    letter-spacing: 2px;
    text-transform: uppercase;
    color: var(--emboss);
    text-align: center;
    line-height: 1.25;
  }
  /* Back */
  .brand-name {
    position: absolute;
    left: 40px;
    top: 34px;
    font-family: 'Montserrat', sans-serif;
    font-weight: 700;
    font-size: 22px;
    letter-spacing: 1.5px;
    text-transform: uppercase;
    color: var(--white);
    line-height: 1.2;
  }
  .person {
    position: absolute;
    left: 40px;
    top: 118px;
  }
  .person-name {
    font-family: 'Montserrat', sans-serif;
    font-weight: 600;
    font-size: 19px;
    text-transform: uppercase;
    color: var(--red);
  }
  .person-role {
    font-family: 'Roboto', sans-serif;
    font-size: 12px;
    color: var(--white);
    margin-top: 2px;
  }
  .contact-list {
    position: absolute;
    left: 40px;
    top: 190px;
    list-style: none;
    font-family: 'Roboto', sans-serif;
    font-size: 14px;
    color: var(--white);
  }
  .contact-list li {
    display: flex;
    align-items: center;
    gap: 12px;
    height: 26px;
  }
  .contact-list svg {
    width: 13px;
    height: 13px;
    fill: var(--red);
    flex: none;
  }
  .brand-panel {
    position: absolute;
    left: 405px;
    top: 64px;
    width: 190px;
    bottom: 0;
    background: var(--red);
    display: flex;
    align-items: center;
    justify-content: center;
  }
  .brand-panel-name {
    font-family: 'Montserrat', sans-serif;
    font-weight: 700;
    font-size: 13px;
    letter-spacing: 1px;
    line-height: 1.4;
    text-transform: uppercase;
    text-align: center;
    color: var(--white);
  }
</style>
</head>
<body>
<main class="canvas">
  <section class="card card-front" aria-label="Voorkant visitekaartje">
    <p class="front-name">Rijwielwerkplaats<br>Vanhoutte</p>
  </section>

  <section class="card card-back" aria-label="Achterkant visitekaartje">
    <p class="brand-name">Rijwielwerkplaats<br>Vanhoutte</p>
    <div class="person">
      <p class="person-name">Marieke Segers</p>
      <p class="person-role">Owner</p>
    </div>
    <ul class="contact-list">
      <li>
        <svg viewBox="0 0 24 24" aria-hidden="true"><path d="M6.6 10.8a15.1 15.1 0 0 0 6.6 6.6l2.2-2.2c.3-.3.7-.4 1-.2 1.1.4 2.3.6 3.6.6.6 0 1 .4 1 1V20c0 .6-.4 1-1 1A17 17 0 0 1 3 4c0-.6.4-1 1-1h3.5c.6 0 1 .4 1 1 0 1.3.2 2.5.6 3.6.1.3 0 .7-.2 1z"/></svg>
        +32471902368
      </li>
      <li>
        <svg viewBox="0 0 24 24" aria-hidden="true"><path d="M2 5h20v14H2zm2 2v.5l8 5 8-5V7l-8 5z"/></svg>
        www.rijwielwerkplaats-vanhoutte.be
      </li>
      <li>
        <svg viewBox="0 0 24 24" aria-hidden="true"><path d="M12 2a10 10 0 1 0 0 20 10 10 0 0 0 0-20zm6.9 6h-3a15 15 0 0 0-1.3-3.6A8 8 0 0 1 18.9 8zM12 4c.8 1.2 1.5 2.5 1.9 4h-3.8c.4-1.5 1.1-2.8 1.9-4zM4.3 14a8 8 0 0 1 0-4h3.4a16 16 0 0 0 0 4zm.8 2h3a15 15 0 0 0 1.3 3.6A8 8 0 0 1 5.1 16zm3-8h-3a8 8 0 0 1 4.3-3.6C8.8 5.6 8.4 6.8 8.1 8zM12 20c-.8-1.2-1.5-2.5-1.9-4h3.8c-.4 1.5-1.1 2.8-1.9 4zm2.3-6H9.7a14 14 0 0 1 0-4h4.6a14 14 0 0 1 0 4zm.3 5.6c.6-1.1 1-2.3 1.3-3.6h3a8 8 0 0 1-4.3 3.6zm1.7-5.6a16 16 0 0 0 0-4h3.4a8 8 0 0 1 0 4z"/></svg>
        info@rijwielwerkplaats-vanhoutte.be
      </li>
      <li>Kerkweg 46 9940 Bellebeke</li>
    </ul>
    <div class="brand-panel">
      <p class="brand-panel-name">Rijwielwerkplaats<br>Vanhoutte</p>
    </div>
  </section>
</main>
</body>
</html>
```